Kellwyn Surface Records

I have a current web site that it looking quite aged and it needs a new lease of life. This is a Graffiti Management Website so is all about data processing and management of information. I want a html 5 view on any platform design. clean crisp and new. I have provided some screen shots of my current site.

Target Market(s)

The Target Market will be local government. most users will not be heavy pc users

Industry/Entity Type

Management

Font styles to use
Sans Serif
Other font styles liked:
• web font like calibri

Colors

Designer to choose colors to be used in the design.

Requirements
Must have
• Must have menus similar to attachments

```html
<!DOCTYPE html>
<html lang="en">
<head>
<meta charset="utf-8">
<title>Kellwyn Surface Records</title>
<link rel="stylesheet" href="https://fonts.googleapis.com/css2?family=Open+Sans:wght@400;600;700&family=Arimo:wght@400;700&display=swap">
<style>
:root{
  --navy:#121a6e;
  --sky:#4aaee3;
  --sky-dark:#3b97c8;
  --text:#555;
  --muted:#777;
  --band:#f4f4f4;
  --footer:#2b2b2b;
  --green:#7bb928;
}
*{margin:0;padding:0;box-sizing:border-box}
html,body{width:790px;height:1200px;overflow:hidden;background:#fff}
body{position:relative;font-family:Arimo,Arial,sans-serif;color:var(--text)}
.abs{position:absolute}
.head{font-family:"Open Sans",Arial,sans-serif}

/* header */
.brand{left:114px;top:16px;color:var(--sky);font:700 25px "Open Sans",sans-serif;letter-spacing:22px}
.brand-sub{left:114px;top:44px;color:var(--navy);font:700 8.5px "Open Sans",sans-serif;letter-spacing:.6px;text-transform:uppercase}
.btn{background:var(--sky);color:#fff;font:700 8px Arimo,sans-serif;text-align:center;line-height:20px;border-bottom:2px solid var(--sky-dark);border-radius:2px}
.nav{top:46px;font:400 7.2px "Open Sans",sans-serif;color:#555;text-transform:uppercase}
.header-line{left:0;top:65px;width:790px;height:1px;background:#e3e3e3}

/* hero */
.hero{left:0;top:66px;width:790px;height:338px;background:linear-gradient(180deg,#a9cde6 0%,#d4e6f1 30%,#9fc3d6 40%,#e7e6e2 55%,#efece6 100%)}
.hero-title{left:82px;top:180px;color:var(--navy);font:700 21px "Open Sans",sans-serif}
.hero-title2{left:82px;top:206px;color:var(--navy);font:400 21px "Open Sans",sans-serif}
.hero-copy{left:82px;top:234px;width:290px;font:400 10px/16px "Open Sans",sans-serif;color:#333}
.arrow{top:277px;width:17px;height:17px;background:#8d8d8d}

/* welcome */
.welcome{left:0;width:790px;text-align:center}
.card-img{top:501px;width:127px;height:88px}
.card-title{top:598px;color:var(--navy);font:400 10px "Open Sans",sans-serif}
.card-copy{top:613px;width:128px;font-size:6.6px;line-height:12.8px;color:#555}

/* who / about */
.sec-title{color:var(--navy);font:600 11px "Open Sans",sans-serif;top:705px}
.tick-list{left:113px;top:733px;width:280px;list-style:none}
.tick-list li{position:relative;padding-left:15px;font-size:7.2px;line-height:12.8px;margin-bottom:6.5px;color:#444}
.tick-list svg{position:absolute;left:0;top:1px}
.about{left:418px;top:734px;width:250px;font-size:6.6px;line-height:12.8px;color:#555}
.about p{margin-bottom:12.8px}

/* testimonial */
.band{left:0;top:927px;width:790px;height:139px;background:var(--band)}
.quote-mark{color:#d2d2d2;font:700 30px Georgia,serif}
.chev{top:990px}

/* partners */
.partner{top:1092px;font:400 15px "Open Sans",sans-serif;color:#555;display:flex;align-items:center;gap:5px}
.partner i{display:inline-block;width:15px;height:15px;border:1.8px solid #666;border-radius:50%}

/* footer */
.footer{left:0;top:1140px;width:790px;height:60px;background:var(--footer)}
.foot-nav{top:1157px;font-size:6.6px;color:#999}
.copy{left:114px;top:1173px;font-size:6.6px;color:#888}
.social{top:1161px;width:10px;height:10px;border-radius:50%;border:1.3px solid #888}
</style>
</head>
<body>

<header>
  <div class="abs brand">KSR</div>
  <div class="abs brand-sub">Kellwyn Surface Records</div>
  <div class="abs btn" style="left:525px;top:12px;width:61px">LOGIN</div>
  <div class="abs btn" style="left:592px;top:12px;width:85px">DEMO LOGIN</div>
  <nav>
    <span class="abs nav" style="left:350px">Products</span>
    <span class="abs nav" style="left:422px">Reports</span>
    <span class="abs nav" style="left:488px">Benifits</span>
    <span class="abs nav" style="left:552px">Legislation</span>
    <span class="abs nav" style="left:631px">Contact Us</span>
  </nav>
  <div class="abs header-line"></div>
</header>

<section>
  <div class="abs hero" role="img" aria-label="Businessman relaxing in a wooden deck chair on a sunny beach, working on a laptop"></div>
  <h1 class="abs hero-title">HELPING YOU</h1>
  <div class="abs hero-title2">CLEAN UP YOUR COMMUNITY</div>
  <p class="abs hero-copy">KSR is an Online Database System to Manage Graffiti in your area or Your Properties</p>
  <div class="abs arrow" style="left:83px"><svg width="17" height="17"><path d="M10 5 6.5 8.5 10 12" fill="none" stroke="#fff" stroke-width="1"/></svg></div>
  <div class="abs arrow" style="left:102px"><svg width="17" height="17"><path d="M7 5 10.5 8.5 7 12" fill="none" stroke="#fff" stroke-width="1"/></svg></div>
</section>

<section>
  <h2 class="abs welcome head" style="top:433px;color:var(--navy);font-size:14.5px;font-weight:700">WELCOME TO KSR</h2>
  <p class="abs welcome" style="top:460px;font-size:9.6px;color:#555">KSR is an Online Database System to Manage Graffiti in your area or Your Properties</p>

  <div class="abs card-img" style="left:113px;background:linear-gradient(135deg,#2b4fa8,#9fc8ef)" role="img" aria-label="Woman touching a digital data interface"></div>
  <div class="abs card-img" style="left:259px;background:linear-gradient(135deg,#f1eef2,#c8bfd0 70%,#5a3a2a)" role="img" aria-label="Hand sketching a flowchart on a notepad"></div>
  <div class="abs card-img" style="left:404px;background:linear-gradient(135deg,#cfd6dd,#eef0f1 50%,#6b87a8)" role="img" aria-label="Smiling woman working on a laptop"></div>
  <div class="abs card-img" style="left:550px;background:linear-gradient(135deg,#8f959b,#d9dbdd 60%,#a7abaf)" role="img" aria-label="Two businessmen shaking hands"></div>

  <h3 class="abs card-title" style="left:113px">PRODUCTS</h3>
  <h3 class="abs card-title" style="left:259px">REPORTS</h3>
  <h3 class="abs card-title" style="left:404px">BENIFITS</h3>
  <h3 class="abs card-title" style="left:550px">LEGISLATION</h3>
  <p class="abs card-copy" style="left:113px">Provides a National Register of Vandalism and Graffiti. Subscribers to the KSR Database can Add, Change, Report on and Archive their own Graffiti Jobs.</p>
  <p class="abs card-copy" style="left:259px">Provides a National Register of Vandalism and Graffiti. Subscribers to the KSR Database can Add, Change, Report on and Archive their own Graffiti Jobs.</p>
  <p class="abs card-copy" style="left:404px">Provides a National Register of Vandalism and Graffiti. Subscribers to the KSR Database can Add, Change, Report on and Archive their own Graffiti Jobs.</p>
  <p class="abs card-copy" style="left:550px">Provides a National Register of Vandalism and Graffiti. Subscribers to the KSR Database can Add, Change, Report on and Archive their own Graffiti Jobs.</p>
</section>

<section>
  <h2 class="abs sec-title" style="left:114px">WHO WE ARE?</h2>
  <ul class="abs tick-list">
    <li><svg width="10" height="8"><path d="M1 4 4 7 9 1" fill="none" stroke="#7bb928" stroke-width="1.8"/></svg>KSR is an Online Database System to Manage Graffiti in your area or Your Properties</li>
    <li><svg width="10" height="8"><path d="M1 4 4 7 9 1" fill="none" stroke="#7bb928" stroke-width="1.8"/></svg>KSR allows you to Register, Track, Report and Archive Graffiti Jobs with Photographic Records.</li>
    <li><svg width="10" height="8"><path d="M1 4 4 7 9 1" fill="none" stroke="#7bb928" stroke-width="1.8"/></svg>KSR records both Estimated and Actual hours and costs for each job, enabling you to track the effectiveness of Anti Graffiti policy</li>
    <li><svg width="10" height="8"><path d="M1 4 4 7 9 1" fill="none" stroke="#7bb928" stroke-width="1.8"/></svg>KSR allows sharing of Critical Graffiti Tag and Photographic Data between its subscribers, assisting with tracking down Serial Graffiti Offenders.</li>
    <li><svg width="10" height="8"><path d="M1 4 4 7 9 1" fill="none" stroke="#7bb928" stroke-width="1.8"/></svg>KSR has a Statistical and Comparison Reporting Systems to allow its subscribers to graphically report and compare their Graffiti Data.</li>
  </ul>

  <h2 class="abs sec-title" style="left:418px">ABOUT US</h2>
  <div class="abs about">
    <p>Lorem Ipsum is simply dummy text of the printing and typesetting industry. Lorem Ipsum has been the industry's standard dummy text ever since the 1500s, when an unknown printer took a galley of type and scrambled.</p>
    <p>Lorem Ipsum is simply dummy text of the printing and typesetting industry. Lorem Ipsum has been the industry's standard dummy text ever since the 1500s, when an unknown printer took a galley of type and scrambled it to make a type specimen book.</p>
  </div>
  <div class="abs btn" style="left:418px;top:855px;width:78px;height:23px;line-height:21px">READ MORE</div>
</section>

<section>
  <div class="abs band"></div>
  <h2 class="abs welcome head" style="top:946px;color:var(--navy);font-size:11px;font-weight:600">WHAT CLIENTS SAY</h2>
  <div class="abs quote-mark" style="left:190px;top:958px">“</div>
  <div class="abs quote-mark" style="left:567px;top:1020px">”</div>
  <p class="abs welcome head" style="top:975px;font-size:10.5px;color:var(--sky)">Milo Hartwell <span style="font-size:7.5px;color:#222;font-style:italic">Marketing Executive</span></p>
  <p class="abs welcome head" style="top:997px;left:220px;width:350px;font-size:6.4px;line-height:12.8px;color:#555">Content here, content here', making it look like readable English. Many desktop publishing packages and web page editors now use Lorem Ipsum as their default model text, and a search for 'lorem ipsum' will uncover many web sites still in their infancy.</p>
  <svg class="abs chev" style="left:114px" width="10" height="22"><path d="M8 1 2 11 8 21" fill="none" stroke="#bbb"/></svg>
  <svg class="abs chev" style="left:660px" width="10" height="22"><path d="M2 1 8 11 2 21" fill="none" stroke="#bbb"/></svg>
</section>

<section>
  <svg class="abs" style="left:98px;top:1100px" width="6" height="8"><path d="M5 1 1 4 5 7" fill="none" stroke="#777"/></svg>
  <div class="abs partner" style="left:126px"><i></i>brightloop</div>
  <div class="abs partner" style="left:249px;font-size:10px;letter-spacing:1px;top:1096px">NORTHKEEP</div>
  <div class="abs partner" style="left:354px;font-weight:700;font-size:13px">VANTEL</div>
  <div class="abs partner" style="left:470px"><i></i>mocha</div>
  <div class="abs partner" style="left:582px;letter-spacing:1px">ROUNDEL</div>
  <svg class="abs" style="left:685px;top:1100px" width="6" height="8"><path d="M1 1 5 4 1 7" fill="none" stroke="#777"/></svg>
</section>

<footer>
  <div class="abs footer"></div>
  <span class="abs foot-nav" style="left:114px">Home</span>
  <span class="abs foot-nav" style="left:147px">Products</span>
  <span class="abs foot-nav" style="left:196px">Reports</span>
  <span class="abs foot-nav" style="left:235px">Benifits</span>
  <span class="abs foot-nav" style="left:272px">Legislation</span>
  <span class="abs foot-nav" style="left:322px">Contact Us</span>
  <p class="abs copy">Copyrights © KSR. All Rights Reserved.</p>
  <span class="abs social" style="left:594px"></span>
  <span class="abs social" style="left:618px"></span>
  <span class="abs social" style="left:641px"></span>
  <span class="abs social" style="left:665px"></span>
</footer>

</body>
</html>
```